New Business card design to reflect rebrand

I would like a business card design with a good base colour for our new logo and also a placeholder for a profile pic of the card holder. the design needs to be editable to the point that we can easily change the picture of the person and use that design for printmerlo etc. we are looking at a metalic finish business card so will need a good base colour to bring out the finish.

Target Market(s)

prospective customers

Industry/Entity Type

Business

Contact Information for Business Card

I would like one editable design that we can change the name of the card holder and profile picture. The design need to be in a format that be send to printmerlo etc.

Our address is Fenwick Lodge, Copse Lane, Ashcombe Vale, GU14 3TP Tel no. 01483 556172

Requirements
Must have
• place holder for a profile pic for the card holder. in AI or preferably PSD format

```html
<!DOCTYPE html>
<html lang="en">
<head>
<meta charset="utf-8">
<title>Halverd Workplace Services – Business Card</title>
<link rel="stylesheet" href="https://fonts.googleapis.com/css2?family=Open+Sans:wght@400;600;700&display=swap">
<style>
  :root {
    --navy: #3d5470;
    --orange: #ec6101;
    --white: #ffffff;
    --backdrop: #e9e9eb;
    --photo-top: #c98f6b;
    --photo-bottom: #2b3140;
  }
  * { box-sizing: border-box; margin: 0; padding: 0; }
  html, body {
    width: 1200px; height: 900px; overflow: hidden;
    background: var(--backdrop);
    font-family: "Open Sans", Arial, sans-serif;
  }
  .stage { position: relative; width: 1200px; height: 900px; }

  .card {
    position: absolute;
    background: var(--white);
    overflow: hidden;
    box-shadow: 0 6px 18px rgba(0,0,0,0.18);
  }

  /* Front: brand and contact */
  .card-front { left: 78px; top: 34px; width: 588px; height: 364px; }
  .brand {
    position: absolute; left: 0; top: 100px; width: 588px;
    display: flex; align-items: center; justify-content: center; gap: 16px;
    color: var(--navy); font-weight: 700;
  }
  .brand-square { width: 34px; height: 34px; background: var(--navy); }
  .brand-name { font-size: 50px; letter-spacing: 3px; line-height: 1; }
  .brand-sub {
    position: absolute; left: 0; top: 159px; width: 588px; text-align: center;
    color: var(--navy); font-weight: 700; font-size: 20px; letter-spacing: 4px;
  }
  .front-bands { position: absolute; left: 0; top: 208px; }
  .contact {
    position: absolute; top: 276px; color: var(--white);
    font-size: 15.5px; line-height: 25px;
  }
  .contact-address { right: 280px; text-align: right; }
  .contact-lines { left: 332px; }
  .contact-line { display: flex; align-items: center; gap: 7px; }
  .contact-line svg { width: 13px; height: 13px; fill: var(--white); }

  /* Back: card holder */
  .card-back { left: 388px; top: 505px; width: 566px; height: 352px; }
  .holder-band { position: absolute; left: 0; top: 0; width: 566px; height: 250px; background: var(--orange); }
  .holder-photo {
    position: absolute; left: 134px; top: 0; width: 276px; height: 250px;
    background: linear-gradient(180deg, var(--photo-top) 0%, var(--photo-top) 55%, var(--photo-bottom) 100%);
    border-radius: 130px 130px 0 0;
  }
  .holder-name {
    position: absolute; left: 0; top: 268px; width: 566px; text-align: center;
    font-weight: 700; font-size: 52px; line-height: 70px; color: var(--navy);
  }
  .holder-name .surname { color: var(--orange); }
</style>
</head>
<body>
<main class="stage">
  <section class="card card-front" aria-label="Business card front">
    <div class="brand">
      <span class="brand-square"></span>
      <span class="brand-name">HALVERD</span>
    </div>
    <div class="brand-sub">WORKPLACE SERVICES</div>

    <svg class="front-bands" width="588" height="156" viewBox="0 0 588 156" aria-hidden="true">
      <polygon points="0,3 415,3 588,3 588,156 0,156 0,47 388,47 415,3" fill="var(--orange)"/>
      <polygon points="0,13 402,13 385,39 0,39" fill="var(--navy)"/>
    </svg>

    <div class="contact contact-address">
      <div>Fenwick Lodge, Copse Lane,</div>
      <div>Ashcombe Vale, GU14 3TP</div>
    </div>
    <div class="contact contact-lines">
      <div class="contact-line">
        <svg viewBox="0 0 24 24" aria-hidden="true"><path d="M6.6 10.8a15.1 15.1 0 0 0 6.6 6.6l2.2-2.2a1 1 0 0 1 1-.25 11.4 11.4 0 0 0 3.6.57 1 1 0 0 1 1 1V20a1 1 0 0 1-1 1A17 17 0 0 1 3 4a1 1 0 0 1 1-1h3.5a1 1 0 0 1 1 1c0 1.25.2 2.45.57 3.57a1 1 0 0 1-.25 1z"/></svg>
        <span>01483 556172</span>
      </div>
      <div class="contact-line">
        <svg viewBox="0 0 24 24" aria-hidden="true"><path d="M2 5h20v14H2z" fill="var(--white)"/><path d="M3 6l9 7 9-7" fill="none" stroke="var(--orange)" stroke-width="2"/></svg>
        <span>info@halverd.com</span>
      </div>
    </div>
  </section>

  <section class="card card-back" aria-label="Business card back">
    <div class="holder-band"></div>
    <div class="holder-photo" role="img" aria-label="Profile photo of the card holder"></div>
    <div class="holder-name">Daniel <span class="surname">Hart</span></div>
  </section>
</main>
</body>
</html>
```